Corporate Business Card

Very professional, Modern, Not to busy, include phone address email, website
(253) 617-4930, 18761 52nd Avenue S, Kent, WA 98047, martin@plumlinegroup.com, varkoworks.com

Target Market(s)

Manufacturing

Industry/Entity Type

Aero, machining, manufacturing, Off road racing

Contact Information for Business Card

Phone, address email, website

```html
<!DOCTYPE html>
<html lang="en">
<head>
<meta charset="utf-8">
<title>Varko Works — Business Card</title>
<link rel="stylesheet" href="https://fonts.googleapis.com/css2?family=Montserrat:wght@500;700&display=swap">
<style>
  :root {
    --brand-red: #d2232a;
    --brand-navy: #1b3a78;
    --card-white: #ffffff;
    --ink: #1a1a1a;
    --backdrop: #2e2e2e;
  }
  * { box-sizing: border-box; margin: 0; padding: 0; }
  html, body { width: 1200px; height: 960px; overflow: hidden; }
  body {
    background: var(--backdrop);
    font-family: "Montserrat", sans-serif;
    position: relative;
  }
  .card {
    position: absolute;
    width: 700px;
    height: 400px;
    overflow: hidden;
    box-shadow: 0 10px 30px rgba(0,0,0,0.45);
  }
  .card-front {
    left: 70px;
    top: 60px;
    background: var(--brand-red);
    display: flex;
    align-items: center;
    justify-content: center;
  }
  .brand-name {
    font-weight: 700;
    letter-spacing: 2px;
    text-transform: uppercase;
    white-space: nowrap;
  }
  .card-front .brand-name {
    color: var(--card-white);
    font-size: 68px;
  }
  .card-back {
    left: 430px;
    top: 500px;
    background: var(--card-white);
  }
  .card-back .brand-name {
    position: absolute;
    right: 48px;
    top: 52px;
    color: var(--brand-navy);
    font-size: 42px;
  }
  .address {
    position: absolute;
    left: 48px;
    top: 150px;
    font-size: 17px;
    font-weight: 500;
    line-height: 1.45;
    color: var(--ink);
  }
  .contact-list {
    position: absolute;
    left: 48px;
    top: 228px;
    list-style: none;
    font-size: 17px;
    font-weight: 500;
    color: var(--ink);
  }
  .contact-list li {
    display: flex;
    align-items: center;
    gap: 10px;
    height: 28px;
  }
  .contact-icon { width: 16px; height: 16px; fill: var(--brand-red); flex: none; }
  .wave { position: absolute; left: 0; bottom: 0; width: 700px; height: 170px; }
  .wave .band { fill: var(--brand-red); }
  .wave .stripe { fill: var(--brand-navy); }
</style>
</head>
<body>

  <section class="card card-front" aria-label="Card front">
    <span class="brand-name">Varko Works</span>
  </section>

  <section class="card card-back" aria-label="Card back">
    <span class="brand-name">Varko Works</span>

    <p class="address">18761 52nd Avenue<br>S, Kent, WA 98047</p>

    <ul class="contact-list">
      <li>
        <svg class="contact-icon" viewBox="0 0 24 24" aria-hidden="true"><path d="M6.6 10.8a15.1 15.1 0 0 0 6.6 6.6l2.2-2.2c.3-.3.7-.4 1-.2 1.1.4 2.3.6 3.6.6.6 0 1 .4 1 1V20c0 .6-.4 1-1 1A17 17 0 0 1 3 4c0-.6.4-1 1-1h3.5c.6 0 1 .4 1 1 0 1.3.2 2.5.6 3.6.1.3 0 .7-.2 1z"/></svg>
        (253) 617-4930
      </li>
      <li>
        <svg class="contact-icon" viewBox="0 0 24 24" aria-hidden="true"><path d="M2 5h20v14H2z M2 5l10 8 10-8" fill="none" stroke="#d2232a" stroke-width="2.4"/></svg>
        martin@plumlinegroup.com
      </li>
      <li>
        <svg class="contact-icon" viewBox="0 0 24 24" aria-hidden="true"><circle cx="12" cy="12" r="10" fill="none" stroke="#d2232a" stroke-width="2.2"/><path d="M2 12h20M12 2c3 3 3 17 0 20M12 2c-3 3-3 17 0 20" fill="none" stroke="#d2232a" stroke-width="1.8"/></svg>
        www.varkoworks.com
      </li>
    </ul>

    <svg class="wave" viewBox="0 0 700 170" preserveAspectRatio="none" aria-hidden="true">
      <path class="stripe" d="M0 150 C 180 150, 300 110, 430 60 C 540 18, 630 4, 700 0 L700 6 C 630 12, 545 28, 440 70 C 310 122, 190 162, 0 165 Z"/>
      <path class="band" d="M0 170 L0 168 C 190 164, 315 128, 445 78 C 550 38, 635 18, 700 12 L700 170 Z"/>
    </svg>
  </section>

</body>
</html>
```